Need a landing page design updated

Need an existing landing page perfected, want it too look similar to one of Quorbel's landing pages in that it flows and is really aesthetically pleasing. The link to the landing page is below. I need this design updated asap. Please take the content directly from the page.

http://verdantmoxfl.com/residential-services/

Target Market(s)

High end residential landscape customers on the gulf coast of Florida (Clearwater area)

Industry/Entity Type

Landscape Gardening

Font styles to use
Sans Serif
Decorative

Requirements
Must have
• I want to keep the written content the same on on the landing page, but would like to work on making both aesthetically appealing to the consumer. This is for high end residential clients on the gulf coast of florida, so think palm trees and sunny beaches with beautiful houses and gorgeous landscapes....look through www.verdantmoxfl.com home page for an example of the houses we landscape.
Nice to have
• Would like it to flow as you scroll similar to Quorbel's landing pages.
• Look at how Quorbel's landing page flows, want similar here.....
• https://www.quorbel.com/zentaphone-v/
Should not have
• this landing page must be beautiful and must make a lot of sense as you scroll, am looking for a work of art....please do not submit generic templates or anything that can be easily done....I need real artistry.

```html
<!DOCTYPE html>
<html lang="en">
<head>
<meta charset="utf-8">
<title>Verdantmox – Residential Landscaping</title>
<link href="https://fonts.googleapis.com/css2?family=Open+Sans:wght@300;400;600;700&family=Raleway:wght@400;500;600&display=swap" rel="stylesheet">
<style>
:root{
  --brand:#0aa3d1;
  --brand-dark:#0b6f8c;
  --brand-deep:#0d5a73;
  --footer:#3bbde0;
  --ink:#333;
  --muted:#666;
  --light:#f2f2f2;
  --white:#fff;
  --dark-band:#2b2e30;
}
*{box-sizing:border-box;margin:0;padding:0}
html,body{width:1200px;height:3689px;overflow:hidden}
body{font-family:"Open Sans",Arial,sans-serif;color:var(--ink);background:var(--white);position:relative}
section,header,footer,nav{position:absolute;left:0;width:1200px}

.site-header{top:0;height:91px;background:var(--white)}
.brand{position:absolute;left:86px;top:26px;display:flex;align-items:center;gap:10px;font-size:30px;font-weight:600;color:var(--brand);letter-spacing:1px}
.brand-dot{width:18px;height:18px;border-radius:50%;background:var(--brand)}
.header-contact{position:absolute;right:90px;top:34px;text-align:right;font-size:13px;line-height:20px;color:var(--ink)}
.header-contact .call{color:var(--brand)}

.main-nav{top:91px;height:37px;background:var(--brand);display:flex;align-items:center;padding-left:94px;gap:26px}
.main-nav a{color:var(--white);font-size:12px;font-weight:700;text-decoration:none;letter-spacing:.3px}

.hero{top:128px;height:474px;background:linear-gradient(180deg,#7c8a7d 0%,#5c6b50 35%,#3f5a2c 70%,#4d7a2e 100%)}
.hero-copy{position:absolute;left:88px;top:170px;color:var(--white)}
.hero-copy h1{font-size:46px;font-weight:400;margin-bottom:8px}
.hero-copy p{font-size:22px;line-height:32px;font-weight:400}

.intro{top:602px;height:264px;text-align:center}
.intro p{position:absolute;left:0;width:1200px;top:68px;font-size:17px;line-height:28px;color:var(--ink)}
.intro p span{font-size:21px;line-height:30px;display:block;color:#222}

.pitch{top:866px;height:157px;background:var(--light);text-align:center}
.pitch p{position:absolute;left:0;width:1200px;top:36px;font-size:17px;line-height:28px}
.pitch p span{display:block;font-size:21px;line-height:30px}

.compare{top:1023px;height:435px;display:flex}
.compare-col{width:600px;height:435px;padding:60px 0 0 88px;color:var(--white)}
.compare-generic{background:linear-gradient(135deg,#18b4e0,#0894c4);border-right:2px solid #0f8fb9}
.compare-tailored{background:linear-gradient(135deg,#0e6d8b,#0a5570);padding-left:42px}
.compare-col h2{font-size:27px;font-weight:600;margin-bottom:28px}
.compare-col ul{list-style:none}
.compare-col li{display:flex;gap:12px;font-size:17px;line-height:26px;margin-bottom:22px;max-width:470px}
.compare-col li svg{flex:none;margin-top:5px}

.expertise{top:1458px;height:477px}
.expertise .photo{position:absolute;left:115px;top:116px;width:401px;height:251px;background:linear-gradient(160deg,#6f8f3a,#8aa84c 45%,#c9c08a 70%,#4e6d2a)}
.expertise-copy{position:absolute;left:560px;top:130px;width:540px}
.expertise-copy h2{font-size:24px;font-weight:400;line-height:34px;color:#444;margin-bottom:14px}
.expertise-copy p{font-size:14px;line-height:24px;color:var(--muted)}

.schedule{top:1935px;height:445px;background:linear-gradient(180deg,#24282a,#3a3d3c 60%,#2a2d2d)}
.schedule-card{position:absolute;left:150px;top:89px;width:497px;height:295px;background:var(--white);padding:56px 40px 0 36px}
.schedule-card h2{font-size:24px;font-weight:400;line-height:34px;color:#222;margin-bottom:18px}
.schedule-card p{font-size:13px;line-height:24px;color:#444}
.schedule .photo{position:absolute;left:647px;top:89px;width:401px;height:295px;background:linear-gradient(180deg,#9fc7e6 0%,#c9dcea 30%,#5f7e3b 55%,#d9cdb6 72%,#4d7a2e 100%)}

.benefits{top:2380px;height:480px;text-align:center}
.benefits h2{position:absolute;left:0;width:1200px;top:92px;font-size:27px;font-weight:400;color:#333}
.benefit{position:absolute;top:191px;width:290px;text-align:center}
.benefit-icon{width:104px;height:104px;border-radius:50%;background:var(--brand);margin:0 auto 36px;display:flex;align-items:center;justify-content:center}
.benefit p{font-size:14px;line-height:22px;color:var(--muted)}

.flaws{top:2860px;height:342px;background:var(--brand-dark)}
.flaws .photo{position:absolute;left:0;top:0;width:700px;height:342px;background:linear-gradient(180deg,#7ec3ea 0%,#b7def2 35%,#5a8a3c 62%,#7fb24a 100%);clip-path:polygon(0 0,504px 0,664px 342px,0 342px)}
.flaws-copy{position:absolute;left:676px;top:60px;width:460px;color:var(--white)}
.flaws-copy h2{font-size:29px;font-weight:400;line-height:38px;margin-bottom:22px}
.flaws-copy ol{list-style:none;font-size:19px;line-height:28px}
.flaws-copy li{display:flex;gap:8px;margin-bottom:14px}

.cta{top:3202px;height:393px;background:var(--light);text-align:center}
.cta h2{position:absolute;left:0;width:1200px;top:62px;font-family:"Raleway",Arial,sans-serif;font-size:23px;font-weight:400;line-height:34px;color:#333}
.cta h3{position:absolute;left:0;width:1200px;top:136px;font-family:"Raleway",Arial,sans-serif;font-size:19px;font-weight:600;color:#222}
.cta-form{position:absolute;left:342px;top:216px;width:531px}
.cta-form input{display:block;width:531px;height:37px;border:1px solid #cfcfcf;background:var(--white);font-family:inherit;font-size:12px;padding:0 12px;margin-bottom:12px;color:#999}
.cta-form button{display:block;width:138px;height:35px;border:0;background:var(--brand);color:var(--white);font-family:inherit;font-size:12px}

.site-footer{top:3595px;height:94px;background:var(--footer);color:var(--white);text-align:center;font-size:16px;line-height:94px}
</style>
</head>
<body>

<header class="site-header">
  <div class="brand"><span class="brand-dot"></span>Verdantmox</div>
  <div class="header-contact">
    <div><span class="call">Call Us Now On :</span> 727-555-0148</div>
    <div>Client Portal | Get A Free Quote</div>
  </div>
</header>

<nav class="main-nav">
  <a href="#">HOME</a><a href="#">ABOUT US</a><a href="#">RESIDENTIAL</a><a href="#">COMMERCIAL</a><a href="#">BLOG</a><a href="#">CONTACT US</a>
</nav>

<section class="hero" role="img" aria-label="Front of a white luxury home with a manicured lawn, shrubs and flowering beds">
  <div class="hero-copy">
    <h1>Let’s guess:</h1>
    <p>You don’t have an abundance of free time. And,<br>you simply don’t want to spend the little time you have<br>– mowing a lawn and pruning the plants</p>
  </div>
</section>

<section class="intro">
  <p>You would probably like to spend that time the way you should, instead.
    <span>Enjoying the sunset in the privacy of your garden, watching a favorite TV show while lying<br>on a hammock, or throwing an occasional BBQ party with your friends and loved ones.</span></p>
</section>

<section class="pitch">
  <p>Getting an outdoor area of your dreams is not that difficult, nor expensive.
    <span>You can make this happen by getting a help from a landscaping company<br>that offers tailor-made services.</span></p>
</section>

<section class="compare">
  <div class="compare-col compare-generic">
    <h2>Generic landscaping services:</h2>
    <ul>
      <li><svg width="16" height="16" viewBox="0 0 16 16"><circle cx="8" cy="8" r="8" fill="#fff"/><path d="M4.5 8.2l2.3 2.3 4.7-4.8" stroke="#0aa3d1" stroke-width="2" fill="none"/></svg>You pay for the bundle of services, regardless of whether you actually need them</li>
      <li><svg width="16" height="16" viewBox="0 0 16 16"><circle cx="8" cy="8" r="8" fill="#fff"/><path d="M4.5 8.2l2.3 2.3 4.7-4.8" stroke="#0aa3d1" stroke-width="2" fill="none"/></svg>You get a generic service, not adjusted to the specific needs of your outdoor area</li>
      <li><svg width="16" height="16" viewBox="0 0 16 16"><circle cx="8" cy="8" r="8" fill="#fff"/><path d="M4.5 8.2l2.3 2.3 4.7-4.8" stroke="#0aa3d1" stroke-width="2" fill="none"/></svg>The field team thinks of your property as just another task they have to complete</li>
    </ul>
  </div>
  <div class="compare-col compare-tailored">
    <h2>Tailor-made landscaping services:</h2>
    <ul>
      <li><svg width="16" height="16" viewBox="0 0 16 16"><circle cx="8" cy="8" r="8" fill="#fff"/><path d="M4.5 8.2l2.3 2.3 4.7-4.8" stroke="#0b6f8c" stroke-width="2" fill="none"/></svg>You pay only for the services your yard really needs.</li>
      <li><svg width="16" height="16" viewBox="0 0 16 16"><circle cx="8" cy="8" r="8" fill="#fff"/><path d="M4.5 8.2l2.3 2.3 4.7-4.8" stroke="#0b6f8c" stroke-width="2" fill="none"/></svg>You get your garden’s specific issues solved, and specific requirements met</li>
      <li><svg width="16" height="16" viewBox="0 0 16 16"><circle cx="8" cy="8" r="8" fill="#fff"/><path d="M4.5 8.2l2.3 2.3 4.7-4.8" stroke="#0b6f8c" stroke-width="2" fill="none"/></svg>The field team members take their time working on your property</li>
      <li><svg width="16" height="16" viewBox="0 0 16 16"><circle cx="8" cy="8" r="8" fill="#fff"/><path d="M4.5 8.2l2.3 2.3 4.7-4.8" stroke="#0b6f8c" stroke-width="2" fill="none"/></svg>They get to learn all about your vision – and make it a reality</li>
    </ul>
  </div>
</section>

<section class="expertise">
  <div class="photo" role="img" aria-label="Curving garden path lined with yellow lilies and green lawn"></div>
  <div class="expertise-copy">
    <h2>Why should you care that Verdantmox employs the leading industry experts and uses modern, eco-friendly technical solutions?</h2>
    <p>That is why we’re able to transform your lawn into a green carpet and get your plants in a perfect health. All while keeping your vision and your budget on our minds. That is why our services actually enable you to reduce the operating expenses.</p>
  </div>
</section>

<section class="schedule">
  <div class="schedule-card">
    <h2>Do you worry our services are going to disturb you while trying to unwind in the privacy of your own garden?</h2>
    <p>Our Client Service Operators Build A Schedule Around<br>Your Needs –Designed Not To Disturb You At All.</p>
  </div>
  <div class="photo" role="img" aria-label="Cream Mediterranean-style house framed by tall palm trees and a lawn"></div>
</section>

<section class="benefits">
  <h2>More benefits of having a well-maintained yard:</h2>
  <div class="benefit" style="left:106px">
    <div class="benefit-icon"><svg width="50" height="44" viewBox="0 0 50 44"><rect x="4" y="24" width="8" height="16" fill="#fff"/><rect x="17" y="18" width="8" height="22" fill="#fff"/><rect x="30" y="26" width="8" height="14" fill="#fff"/><path d="M4 20l13-10 9 7 16-13" stroke="#fff" stroke-width="3" fill="none"/><path d="M36 3h8v8" stroke="#fff" stroke-width="3" fill="none"/></svg></div>
    <p>In some cases, a great-looking<br>lawn can increase your property’s<br>value up to 20%.</p>
  </div>
  <div class="benefit" style="left:445px">
    <div class="benefit-icon"><svg width="50" height="48" viewBox="0 0 50 48"><path d="M25 3L4 21h6v23h30V21h6z" fill="none" stroke="#fff" stroke-width="3"/><circle cx="25" cy="30" r="9" fill="#fff"/><text x="25" y="35" text-anchor="middle" font-size="13" font-weight="700" fill="#0aa3d1" font-family="Open Sans, sans-serif">$</text></svg></div>
    <p>Your lawn and plants reduce the<br>energy consumption – countering the<br>warming effects of paved surfaces.</p>
  </div>
  <div class="benefit" style="left:780px">
    <div class="benefit-icon"><svg width="54" height="40" viewBox="0 0 54 40"><rect x="14" y="8" width="22" height="24" fill="#fff"/><path d="M2 14h10M2 20h10M2 26h10" stroke="#fff" stroke-width="3"/><path d="M38 10l12 10-12 10z" fill="#fff"/></svg></div>
    <p>They act as giant dust filters, increas-<br>ing air quality, and removing carbon<br>dioxide from the atmosphere</p>
  </div>
</section>

<section class="flaws">
  <div class="photo" role="img" aria-label="Tropical beachfront garden with palm trees, lawn and blue sky"></div>
  <div class="flaws-copy">
    <h2>Do our services have flaws?<br>Yes. They have two giant ones.</h2>
    <ol>
      <li><span>1.</span><span>Your “new” garden will get all of your neighbors jealous.</span></li>
      <li><span>2.</span><span>Your friends will probably start inviting themselves over more frequently.</span></li>
    </ol>
  </div>
</section>

<section class="cta">
  <h2>So, what’s the next step to enriching your living area?<br>And getting you a garden from your dreams.</h2>
  <h3>It’s simple, just book a no-obligations consultation</h3>
  <form class="cta-form">
    <input type="text" placeholder="Name">
    <input type="text" placeholder="Phone OR Email">
    <button type="button">Get Started</button>
  </form>
</section>

<footer class="site-footer">Copyright 2017 Verdantmox All Rights Reserved</footer>

</body>
</html>
```